Redesign of an existing homepage

This site needs a redesign
https://www.wanderhof-kelbach.de
This page with the accommodation options is important for the customer
https://www.wanderhof-kelbach.de/gastgeber/
Till now there is a new logo. See attachment. That's all I have.
It would make sense to use the colors of the logo in the redesign.
footer.jpg.
I would put this info into the footer. The graphic (Infomaterial) is not needed.
a new menu - links.jpg
This info can be put in a new menu. Therefore the right column is gone and there is more space for the design.
NEW:
Please keep in mind that the Icons are important and shall be displayed under every accommodation

```html
<!DOCTYPE html>
<html lang="de">
<head>
<meta charset="utf-8">
<title>Gästeverein Kelbachtal – Freizeit und Erholung</title>
<link rel="stylesheet" href="https://fonts.googleapis.com/css2?family=Outfit:wght@300;400;500;600&display=swap">
<style>
:root{
  --blue:#0b56a4;
  --green:#7ab51d;
  --lime:#c5d400;
  --grey-text:#7a7a7a;
  --dark:#222;
  --soft:#f4f4f4;
  --white:#fff;
}
*{box-sizing:border-box;margin:0;padding:0}
html,body{width:1200px;height:3499px;overflow:hidden}
body{font-family:"Outfit",sans-serif;color:var(--dark);background:var(--white);position:relative}
a{color:inherit;text-decoration:none}
.abs{position:absolute}

/* header */
.site-header{position:absolute;left:0;top:0;width:1200px;height:109px;background:var(--white);border-bottom:1px solid #e6e6e6}
.topbar{position:absolute;right:0;top:0;width:466px;height:48px;background:var(--green);clip-path:polygon(30px 0,100% 0,100% 100%,0 100%)}
.topbar .phone{position:absolute;left:40px;top:13px;color:var(--white);font-size:17px;font-weight:500;display:flex;align-items:center;gap:8px}
.btn{display:inline-block;background:var(--blue);color:var(--white);font-weight:500}
.topbar .btn{position:absolute;left:226px;top:8px;width:99px;height:32px;line-height:32px;text-align:center;font-size:15px}
.brand{position:absolute;left:141px;top:30px;display:flex;align-items:center;gap:10px;color:var(--green);font-size:20px;font-weight:600;line-height:1.1}
.brand .mark{width:26px;height:26px;border-radius:50%;background:var(--green)}
.brand small{display:block;font-size:12px;font-weight:400;letter-spacing:2px;color:var(--grey-text)}
.main-nav{position:absolute;left:480px;top:68px;display:flex;gap:20px;font-size:13px;font-weight:500}
.main-nav .active{color:var(--blue)}

/* hero */
.hero{position:absolute;left:0;top:109px;width:1200px;height:524px;background:linear-gradient(180deg,#8a9ba6 0%,#6f8a5c 30%,#4f7a35 60%,#3f6b2c 100%)}
.hero h1{position:absolute;left:0;width:1200px;top:160px;text-align:center;color:var(--white);font-size:54px;font-weight:500;line-height:72px;text-shadow:0 2px 8px rgba(0,0,0,.35)}
.hero .btn{position:absolute;left:535px;top:303px;width:130px;height:40px;line-height:40px;text-align:center;font-size:20px}

/* section headings */
.section-title{position:absolute;left:0;width:1200px;text-align:center;font-size:33px;font-weight:500;color:var(--grey-text)}
.section-title b{color:var(--blue);font-weight:500}
.section-title::after{content:"";display:block;width:52px;height:3px;background:var(--grey-text);margin:8px auto 0}

/* welcome */
.frame-lime{position:absolute;background:var(--lime)}
.photo{position:absolute}
.welcome-text{position:absolute;left:560px;top:792px;width:500px;font-size:12px;line-height:22px;color:var(--dark)}
.welcome-text h3,.welcome-text .sign{color:var(--green);font-weight:500;font-size:15px}
.welcome-text h3{margin-bottom:4px}
.welcome-text p{margin-bottom:6px}
.welcome-text .sign{margin-top:14px}

/* video */
.video-band{position:absolute;left:0;top:1248px;width:1200px;height:698px;background:var(--soft)}
.video-frame{position:absolute;left:184px;top:1421px;width:826px;height:420px;background:var(--white);border-radius:14px;box-shadow:0 22px 30px -18px rgba(0,0,0,.35);padding:7px}
.video-frame .screen{position:relative;width:100%;height:100%;border-radius:8px;background:linear-gradient(180deg,#b9d0e6 0%,#8fa58a 22%,#6d7f64 60%,#5d6f52 100%)}
.play{position:absolute;left:374px;top:184px;width:64px;height:42px;border:3px solid var(--white);border-radius:8px}
.controls{position:absolute;left:0;right:0;bottom:0;height:36px;background:linear-gradient(0deg,rgba(0,0,0,.45),transparent)}
.controls .bar{position:absolute;left:58px;right:90px;top:18px;height:3px;background:rgba(255,255,255,.5)}

/* stay */
.stay{position:absolute;left:142px;top:2107px;width:500px}
.stay h2{color:var(--blue);font-size:27px;font-weight:500;line-height:34px;margin-bottom:8px}
.stay p{font-size:14px;line-height:25px;margin-bottom:6px}
.stay .btn{width:99px;height:31px;line-height:31px;text-align:center;font-size:15px;margin-top:8px}

/* map */
.map-band{position:absolute;left:0;top:2495px;width:1200px;height:661px;background:var(--soft)}
.map{position:absolute;left:213px;top:2581px;width:573px;height:371px;border:3px solid var(--green);background:linear-gradient(135deg,#eef0ec,#e3e7e1)}
.location{position:absolute;left:836px;top:2675px;font-size:12px;line-height:22px}
.location h2{color:var(--blue);font-size:33px;font-weight:500;line-height:40px}
.location h2::after{content:"";display:block;width:52px;height:3px;background:var(--blue);margin-top:4px}
.location h4{color:var(--grey-text);font-size:16px;font-weight:500;margin:10px 0 4px}
.partners{position:absolute;top:2990px;left:0;width:1200px;display:flex;justify-content:space-around;padding:0 170px}
.partner{width:130px;height:92px;background:#d6dde6;border-radius:6px}
.partner.round{width:80px;border-radius:50%;background:#c9dcae}

/* footer */
.site-footer{position:absolute;left:0;top:3156px;width:1200px;height:343px;background:var(--blue);color:var(--white)}
.fcol{position:absolute;top:78px;font-size:12px;line-height:25px}
.fcol h4{color:var(--lime);font-size:15px;font-weight:500}
.fcol h4::after{content:"";display:block;width:34px;height:2px;background:var(--lime);margin:2px 0 4px}
.fbrand{position:absolute;left:432px;top:96px;display:flex;align-items:center;gap:12px;font-size:24px;font-weight:600;line-height:1.1}
.fbrand .mark{width:34px;height:34px;border-radius:50%;background:var(--white)}
.fbrand small{display:block;font-size:13px;font-weight:400;letter-spacing:3px}
.fcontact{position:absolute;left:395px;top:210px;display:flex;gap:26px;font-size:15px;font-weight:500}
.fcontact span{display:flex;align-items:center;gap:8px}
.frule{position:absolute;left:140px;right:140px;top:292px;height:1px;background:rgba(255,255,255,.3)}
.fbottom{position:absolute;left:143px;right:145px;top:307px;font-size:10px;display:flex;justify-content:space-between}
.fbottom nav{display:flex;gap:18px}
</style>
</head>
<body>

<header class="site-header">
  <div class="brand"><span class="mark"></span><div>Gästeverein Kelbachtal<small>KELBACH UND UMGEBUNG</small></div></div>
  <div class="topbar">
    <span class="phone"><svg width="20" height="20" viewBox="0 0 24 24" fill="none" stroke="#fff" stroke-width="1.8"><path d="M5 3h4l2 5-2.5 1.5a11 11 0 0 0 6 6L16 13l5 2v4a2 2 0 0 1-2 2A17 17 0 0 1 3 5a2 2 0 0 1 2-2z"/></svg>08123 / 456 7890</span>
    <a class="btn" href="#">Kontakt</a>
  </div>
  <nav class="main-nav">
    <a class="active" href="#">Heim</a><a href="#">Kelbach</a><a href="https://www.wanderhof-kelbach.de/gastgeber/">Gastgeber</a><a href="#">Kelbachtal_Aue</a><a href="#">Bäderland</a><a href="#">Tourismusverband Hügelland</a>
  </nav>
</header>

<section class="hero" role="img" aria-label="Luftaufnahme eines Freizeitparks mit Sommerrodelbahn inmitten grüner Wiesen">
  <h1>Freizeit Und Erholung Für Die<br>Ganze Familie</h1>
  <a class="btn" href="#">Kontakt</a>
</section>

<h2 class="section-title" style="top:710px"><b>Urlaub Im Kelbachtal –</b> Dem Schönsten Fleck Bayerns</h2>
<div class="frame-lime" style="left:141px;top:799px;width:394px;height:366px"></div>
<div class="photo" style="left:148px;top:791px;width:387px;height:366px;background:linear-gradient(180deg,#9fb3c2 0%,#3f5e34 30%,#5d8a3b 60%,#6f9a45 100%)" role="img" aria-label="Bauernhof mit roten Dächern vor bewaldeten Hügeln"></div>
<div class="welcome-text">
  <h3>Lieber Besucherinnen und Besucher</h3>
  <p>Kelbach und Umgebung haben all das, was das Leben lebenswert macht: Kultur und Natur, Lebensfreude und Genuss, freundliche &amp; aufgeschlossene Mensche.</p>
  <p>Ob Kirchen, Brunnen oder andere Baudenkmäler – bei einem Rundgang durch die Kelbacher Ross-Stadt kann man viele liebevolle Details für sich entdecken.</p>
  <p>Für Bewegungsfreudige und Erholungssuchende gibt es "Natur pur" in und um Kelbach! Hier kann man sportlich unterwegs sein beim Radeln, Walken, Wandern, Golfen, Reiten und Baden oder einfach nur die Ruhe genießen</p>
  <p>Freizeit und Erholung für die ganze Familie – planen Sie einen Urlaub auf dem Bauernhof, in einer Ferienwohnung oder im Hotel. Ihr Urlaub im Kelbachtal wird ein einmaliges Erlebnis!</p>
  <p>Genießen Sie unsere Gastfreundschaft – ein Besuch lohnt sich zu jeder Jahreszeit.</p>
  <p>Wir freuen uns auf Sie!</p>
  <p class="sign">Ihr… Gästeverein Kelbachtal und Umgebung e. V.</p>
</div>

<div class="video-band"></div>
<h2 class="section-title" style="top:1327px"><b>Video</b> Ansehen</h2>
<div class="video-frame">
  <div class="screen" role="img" aria-label="Video: Luftaufnahme der Kleinstadt Kelbach">
    <div class="play"><svg width="58" height="36" viewBox="0 0 58 36"><path d="M24 10l12 8-12 8z" fill="#fff"/></svg></div>
    <div class="controls"><svg class="abs" style="left:20px;top:12px" width="14" height="14" viewBox="0 0 14 14"><path d="M2 1l11 6-11 6z" fill="#fff"/></svg><div class="bar"></div></div>
  </div>
</div>

<div class="stay">
  <h2>Finde mehr als 7.700.000 Unterkünfte weltweit von Gastgebern auf Stayhub.</h2>
  <p>Sichere Buchung und flexible Stornierungsmöglichkeiten. Jetzt Urlaub sorgenfrei planen! Super Locations.</p>
  <p>Freizeit und Erholung für die ganze Familie – planen Sie einen Urlaub auf dem Bauernhof, in einer Ferienwohnung oder im Hotel</p>
  <a class="btn" href="https://www.wanderhof-kelbach.de/gastgeber/">Kontakt</a>
</div>
<div class="frame-lime" style="left:674px;top:2044px;width:387px;height:366px"></div>
<div class="photo" style="left:667px;top:2037px;width:387px;height:366px;background:linear-gradient(160deg,#e0a452 0%,#a8622a 40%,#6b3f22 75%,#4a2f22 100%)" role="img" aria-label="Beleuchteter Arkadenhof eines Hotels am Abend"></div>

<div class="map-band"></div>
<div class="map" role="img" aria-label="Stadtplan von Kelbach mit Lage des Gästevereins"></div>
<div class="location">
  <h2>Lageplan</h2>
  <h4>Öffnungszeiten</h4>
  <div>Mo–Do &nbsp; 9:00 – 16:00 Uhr</div>
  <div>Fr &nbsp;&nbsp;&nbsp; 9:00 – 12:30 Uhr</div>
  <div style="margin-top:4px">Marktplatz 4</div>
  <div>84399 Kelbach</div>
</div>
<div class="partners">
  <div class="partner"></div><div class="partner"></div><div class="partner" style="width:250px"></div><div class="partner round"></div>
</div>

<footer class="site-footer">
  <div class="fcol" style="left:142px">
    <h4>Schnelle Links</h4>
    <div>Heim</div><div>Kelbach</div><div>Gastgeber</div><div>Kelbachtal_Aue</div><div>Bäderland</div><div>Tourismusverband Hügelland</div>
  </div>
  <div class="fbrand"><span class="mark"></span><div>Gästeverein Kelbachtal<small>KELBACH UND UMGEBUNG</small></div></div>
  <div class="fcontact">
    <span><svg width="22" height="22" viewBox="0 0 24 24" fill="none" stroke="#c5d400" stroke-width="1.8"><path d="M5 3h4l2 5-2.5 1.5a11 11 0 0 0 6 6L16 13l5 2v4a2 2 0 0 1-2 2A17 17 0 0 1 3 5a2 2 0 0 1 2-2z"/></svg>Tel.: 08123 / 456 7890</span>
    <span><svg width="22" height="22" viewBox="0 0 24 24" fill="none" stroke="#c5d400" stroke-width="1.8"><path d="M5 3h4l2 5-2.5 1.5a11 11 0 0 0 6 6L16 13l5 2v4a2 2 0 0 1-2 2A17 17 0 0 1 3 5a2 2 0 0 1 2-2z"/></svg>Fax: 08123 / 456 7891</span>
  </div>
  <div class="fcol" style="left:901px">
    <h4>Das Kelbachtal Entdecken</h4>
    <div>Kirchen im Tal</div><div>Lindmünster</div><div>Eichenfelden</div><div>Bad Wiesbrunn</div><div>Bad Steinquell</div><div>Hollern &amp; Weidach</div>
  </div>
  <div class="frule"></div>
  <div class="fbottom">
    <span>© 2025. Wanderhof-Kelbach. Alle Rechte Vorbehalten</span>
    <nav><a href="#">Informationsmaterial</a><a href="#">Impressum</a><a href="#">Datenschutz</a></nav>
  </div>
</footer>

</body>
</html>
```